9x12 Business Brochure, 3 fold, for Internet Marketing Company

I'd like to have a brochure designed for my Internet marketing company. I have the content all ready, 10 Internet Marketing Myths, which you can see here: http://www.brisklanternstudio.example/usual-web-promotion-fables/. I'm looking for something creative and business to business. The company is all about Internet marketing. I like the "http://" header I use at our website. People like it too and identify with it. Audience is business owners 35 to 55 years old. I use blue at my website. I *think* I would like the cover page (front page) to open with some attention grabbing text, that basically takes most of the front page of the brochure. It would probably say: "I Can Help You Get BETTER RESULTS from Your Website, More Traffic, TOP RANKINGS at Quorble, More Leads and MORE SALES. But first you'll have to avoid these common Internet marketing myths..." The inside pages would have the content from above (the 10 myths). The back page would have testimonials that I can provide. And the inside folded in page (or what I call the inside folded in page) would have a list of services. I think I want the dimensions 12x9 which is a larger sized, three-fold brochure.

Target Market(s)

I use this brochure to send to business owners and managers to show them I know what I'm talking about and and expert. See attachment for content.

Industry/Entity Type

Marketing

Requirements
Should not have
• No clipart. Probably not illustrations. Photos. The "http://" used at the site is something people "connect" with and get that this is about Internet marketing.

```html
<!DOCTYPE html>
<html lang="en">
<head>
<meta charset="utf-8">
<title>Practical Online Marketing – Tri-fold Brochure</title>
<link rel="stylesheet" href="https://fonts.googleapis.com/css2?family=Arimo:ital,wght@0,400;0,700;1,400&display=swap">
<style>
  :root{
    --slate:#5b6b7a;
    --slate-light:#a9b4bf;
    --navy-deep:#0b2452;
    --navy:#1b4683;
    --sky:#5ccbe9;
    --white:#ffffff;
    --ink-grey:#5d6670;
    --paper:#ffffff;
  }
  *{box-sizing:border-box;margin:0;padding:0}
  html,body{width:1200px;height:901px;overflow:hidden;background:#e9ecef}
  body{font-family:"Arimo",Arial,sans-serif;color:var(--white)}
  .brochure{position:absolute;left:0;top:0;width:1200px;height:901px;display:flex}
  .panel{position:relative;width:400px;height:901px;overflow:hidden}

  /* Services panel */
  .services{background:var(--slate)}
  .services__title{position:absolute;left:0;width:400px;top:18px;text-align:center;font-weight:700;font-size:34px;line-height:42px}
  .services__box{position:absolute;left:4px;top:104px;width:376px;height:700px;border-radius:0 14px 14px 0;
    background:linear-gradient(160deg,var(--navy-deep) 0%,var(--navy) 55%,var(--navy-deep) 100%)}
  .services__list{list-style:none;position:absolute;left:40px;top:42px;font-size:17px;line-height:30.5px}
  .services__list li{position:relative;padding-left:20px}
  .services__list li::before{content:"";position:absolute;left:0;top:11px;width:8px;height:8px;background:var(--white)}
  .services__quote{position:absolute;left:0;width:376px;top:650px;text-align:center;font-style:italic;font-size:17px;line-height:27px}
  .services__call{position:absolute;left:0;width:400px;top:836px;text-align:center;font-weight:700;font-size:24px}

  /* Testimonials panel */
  .stories{background:var(--paper)}
  .stories__art{position:absolute;left:90px;top:0;width:300px;height:112px;border-radius:0 0 8px 8px;
    background:radial-gradient(circle at 30% 55%,#2aa3d6 0%,#1b4683 45%,#dfe6ee 75%)}
  .stories__box{position:absolute;left:8px;top:112px;width:384px;height:700px;border-radius:14px;
    background:linear-gradient(180deg,var(--navy-deep) 0%,var(--navy) 50%,var(--navy-deep) 100%)}
  .stories__title{position:absolute;left:20px;top:62px;font-size:38px;font-weight:700}
  .stories__body{position:absolute;left:20px;right:22px;top:120px;font-size:13.4px;line-height:17.5px;text-align:justify}
  .stories__body p{margin-bottom:20px}
  .stories__body b{font-size:16px}
  .stories__sign{position:absolute;left:0;width:400px;top:842px;text-align:center;color:var(--ink-grey);font-weight:700;font-size:17px;line-height:24px}

  /* Cover panel */
  .cover{background:radial-gradient(ellipse at 50% 45%,#dbe1e7 0%,var(--slate-light) 45%,var(--slate) 100%)}
  .cover__title{position:absolute;left:18px;top:0;width:338px;height:170px;border-radius:0 0 12px 12px;
    background:linear-gradient(180deg,var(--navy-deep),var(--navy));text-align:center;font-weight:700;padding-top:26px}
  .cover__title span{display:block}
  .cover__title .t-sm{font-size:32px;line-height:38px}
  .cover__title .t-lg{font-size:44px;line-height:46px}
  .cover__art{position:absolute;left:20px;top:215px;width:360px;height:270px;border-radius:6px;
    background:radial-gradient(ellipse at 55% 50%,#f3f5f7 0%,#b7c1cb 55%,rgba(120,135,150,0) 80%)}
  .cover__pitch{position:absolute;left:0;width:400px;top:500px;text-align:center;font-weight:700;font-size:23px;line-height:31px;color:var(--sky)}
  .cover__pitch .w{color:var(--white)}
  .cover__pitch .big{font-size:31px}
  .cover__myths{position:absolute;left:0;width:400px;top:734px;text-align:center;font-size:18.5px;line-height:24px}
  .cover__contact{position:absolute;left:22px;top:788px;width:356px;height:92px;border-radius:12px;
    background:linear-gradient(180deg,var(--navy-deep),var(--navy));text-align:center;font-weight:700;padding-top:18px}
  .cover__contact .firm{font-size:18px;line-height:24px}
  .cover__contact .phone{font-size:25px;line-height:34px}
</style>
</head>
<body>
<main class="brochure">

  <section class="panel services">
    <h2 class="services__title">Services &amp;<br>Expertise</h2>
    <div class="services__box">
      <ul class="services__list">
        <li>Internet Strategy Development</li>
        <li>Custom Website Design</li>
        <li>Blog Design &amp; Support</li>
        <li>Online Marketing Copywriting</li>
        <li>Social Media Marketing</li>
        <li>Search Engine Optimization (SEO)</li>
        <li>Conversion Optimization</li>
        <li>Content Marketing Management</li>
        <li>Using Chatterbox for Business</li>
        <li>Quorble+, Vidstream, Pinboardly</li>
        <li>Email Marketing &amp; Production</li>
        <li>Inquiry and Lead Development</li>
        <li>Quorble AdSpots Pay-Per-Click</li>
        <li>Quorble Local Places (maps)</li>
        <li>E-Commerce Development</li>
        <li>High-Performance Hosting</li>
        <li>Security &amp; Contingency Planning</li>
        <li>One-on-One or Group Training</li>
      </ul>
      <p class="services__quote">“If you think it’s expensive to hire an<br>expert, &nbsp;wait until you hire an amateur.”</p>
    </div>
    <p class="services__call">Call Us: (555) 014-2273</p>
  </section>

  <section class="panel stories">
    <div class="stories__art" role="img" aria-label="Globe with a web address bar and pointer arrow"></div>
    <div class="stories__box">
      <h2 class="stories__title">Success Stories</h2>
      <div class="stories__body">
        <p><b>Quorble Rankings</b> – “… we have spent over a year trying to get onto page one at Quorble. I has been very frustrating and we’ve wasted a lot of time and money. Dana explained everything very clearly and we did everything he told us. 90 days later we’re now showing up on the first page of Quorble!</p>
        <p><b>Website Design</b> – “We needed a new website that properly reflected our company and the products and services we sell. We started getting more leads within 72 hours of launching the new site Dana and his team designed for us. We’re also getting better results from our Quorble AdSpots pay-per-click advertising and more of those clicks are turning into inquiries!”</p>
        <p><b>More to Come</b> - Lorem ipsum dolor sit amet, consectetur adipiscing elit. Suspendisse justo velit, auctor ut pulvinar a, egestas non urna. Suspendisse potenti. Sed at pellentesque dolor. Vivamus sed nibh nisl. Nunc tortor tellus, facilisis eget pretium vitae, porttitor quis libero.</p>
        <p><b>More to Come</b> - Lorem ipsum dolor sit amet, consectetur adipiscing elit. Suspendisse justo velit, auctor ut pulvinar a, egestas non urna. Suspendisse potenti. Sed at pellentesque dolor. Vivamus sed nibh nisl. Nunc tortor tellus, facilisis eget pretium vitae, porttitor quis libero.</p>
      </div>
    </div>
    <p class="stories__sign">DANA WHITCOMBE<br>Dana Whitcombe Consulting (.com)</p>
  </section>

  <section class="panel cover">
    <h1 class="cover__title">
      <span class="t-sm">PRACTICAL</span>
      <span class="t-lg">Online</span>
      <span class="t-sm">MARKETING</span>
    </h1>
    <div class="cover__art" role="img" aria-label="Three-dimensional WWW letters with a pointer arrow"></div>
    <p class="cover__pitch">
      I Can Help You Get<br>
      <span class="w big">BETTER RESULTS</span><br>
      from Your Website,<br>
      More Traffic,<br>
      <span class="w big">TOP RANKINGS</span> with<br>
      Quorble, More Inquiries, &amp;<br>
      <span class="w big">MORE SALES</span>
    </p>
    <p class="cover__myths">But first you’ll need to avoid these<br>Common Internet Marketing Myths…</p>
    <div class="cover__contact">
      <p class="firm">Dana Whitcombe Consulting (.com)</p>
      <p class="phone">(555) 014-2273</p>
    </div>
  </section>

</main>
</body>
</html>
```